KRT Engineering Business Card Design

We’re looking for an elegant, clean, and timeless business card design that communicates experience, capability, and reliability.

KRT Engineering was established in 1995 , we are a Government Contracting company providing Professional Services to the Office of Frontier Affairs, Harbor Protection and the Vantage Collective. Our capabilities include: Acquisition & Program Management; Intelligence & Security Operations; Cyber, IT & Network Operations; Lifecycle Logistics & Asset Readiness; C5ISR Systems Engineering & Sustainment.

We want the card to reflect a straightforward, confident approach to business. The design should feel polished and professional without being flashy or overly corporate.

Design Direction
Clean, sophisticated, and uncluttered
Elegant but understated
Strong typography and thoughtful spacing
A timeless aesthetic rather than something overly trendy
Confident and established, with a sense of substance
Easy to read and practical in a real-world business setting

The overall impression should be: “These are experienced professionals who know what they’re doing, do what they say, and can be relied upon.”

We’re open to creative interpretations. The finished card should feel distinctive through its typography, proportions, layout, and attention to detail rather than through excessive graphics or visual effects.

We’re looking for a design that would make a potential client immediately feel that they’re dealing with a capable, trustworthy, and established company.

Company Colors: Navy and Gold/Yellow (but you do not need to use these colors on the card)
Company Name: KRT Engineering Associates, Inc. (known as KRT Engineering)
Website: krtengineering.com
Company Logo: Navy & Gold (other variations attached)

```html
<!DOCTYPE html>
<html lang="en">
<head>
<meta charset="utf-8">
<title>KRT Engineering Business Card</title>
<link href="https://fonts.googleapis.com/css2?family=Arimo:wght@400;700&display=swap" rel="stylesheet">
<style>
  :root {
    --navy: #1f2a5e;
    --gold: #f5dc4c;
    --paper: #f3f3f3;
    --ink: #2a2a2a;
    --backdrop: #1d1d1d;
  }
  * { margin: 0; padding: 0; box-sizing: border-box; }
  html, body {
    width: 1200px;
    height: 1059px;
    overflow: hidden;
    background: var(--backdrop);
    font-family: "Arimo", Arial, sans-serif;
  }
  .card {
    position: absolute;
    left: 255px;
    width: 690px;
    height: 390px;
    border-radius: 18px;
    overflow: hidden;
  }
  .card-front { top: 89px; background: var(--paper); }
  .card-back {
    top: 547px;
    background: var(--navy);
    display: flex;
    align-items: center;
    justify-content: center;
  }
  .front-band { position: absolute; inset: 0; width: 690px; height: 390px; }
  .identity { position: absolute; left: 44px; top: 206px; }
  .person-name {
    font-weight: 700;
    font-size: 21px;
    color: var(--navy);
    line-height: 1.1;
  }
  .person-title {
    font-size: 16px;
    color: var(--ink);
    margin-top: 4px;
  }
  .contact-list {
    list-style: none;
    position: absolute;
    left: 44px;
    top: 270px;
  }
  .contact-item {
    display: flex;
    align-items: center;
    gap: 8px;
    font-size: 16px;
    color: var(--ink);
    height: 28.5px;
  }
  .contact-icon { width: 13px; height: 13px; flex: none; }
  .brand-name {
    font-weight: 700;
    font-size: 46px;
    color: var(--paper);
    letter-spacing: 0.5px;
  }
</style>
</head>
<body>
  <section class="card card-front">
    <svg class="front-band" viewBox="0 0 690 390" aria-hidden="true">
      <path d="M0 0 H690 V150 C560 40 300 20 0 150 Z" fill="var(--gold)"/>
      <path d="M0 0 H690 V120 C560 10 300 0 0 136 Z" fill="var(--navy)"/>
    </svg>
    <div class="identity">
      <h1 class="person-name">Laura M. Whitfield</h1>
      <p class="person-title">Principal Engineer</p>
    </div>
    <ul class="contact-list">
      <li class="contact-item">
        <svg class="contact-icon" viewBox="0 0 24 24"><path fill="var(--navy)" d="M6.6 10.8a15 15 0 0 0 6.6 6.6l2.2-2.2a1 1 0 0 1 1-.25 11.4 11.4 0 0 0 3.6.57 1 1 0 0 1 1 1V20a1 1 0 0 1-1 1A17 17 0 0 1 3 4a1 1 0 0 1 1-1h3.5a1 1 0 0 1 1 1c0 1.25.2 2.45.57 3.57a1 1 0 0 1-.25 1z"/></svg>
        (555) 987-2143
      </li>
      <li class="contact-item">
        <svg class="contact-icon" viewBox="0 0 24 24"><path fill="var(--navy)" d="M2 9 12 2l10 7v12H2z"/><path fill="var(--paper)" d="M4 10l8 6 8-6v1l-8 6-8-6z"/></svg>
        l.w@krtengineering.com
      </li>
      <li class="contact-item">
        <svg class="contact-icon" viewBox="0 0 24 24"><circle cx="12" cy="12" r="10" fill="var(--navy)"/><path d="M2 12h20M12 2c3 3 3 17 0 20M12 2c-3 3-3 17 0 20" stroke="var(--paper)" stroke-width="1.5" fill="none"/></svg>
        krtengineering.com
      </li>
    </ul>
  </section>

  <section class="card card-back">
    <p class="brand-name">KRT Engineering</p>
  </section>
</body>
</html>
```